KAJU Freightways #ALLKAJU Business Cards & Letterhead

I am looking to business cards designed for our organization. We are currently undergoing a small re-branding that is taking place. Our organization is called KAJU Freightways and we are headquartered in Phoenix, AZ. We primarily provide transportation and logistics services to the Marlow Parcel Bureau who is our largest customer. I would like to see a design that incorporates name, title, contact info, website, and address (this will be different depending on the employee). I would also like to see some color on the business card using our logo colors or a variation. I would like our logo on the back of the business card with the website displayed. The final design should communicate that we are a next generation transportation operate that focuses on being driver-first, customer-centric, innovative, and sustainable.We would also like our #ALLKAJU catch phrase incorporated as well.

Target Market(s)

Transportation & Logistics

Industry/Entity Type

Trucking Company

Contact Information for Business Card

-First and Last Name
-Position Title
-Contact Phone
-Contact Email
-Physical Address

Font styles to use
Serif

Colors

Designer to choose colors to be used in the design.

Requirements
Must have
• -KAJU logo prominently displayed
• -#ALLKAJU catch phrase used
• -Some amount of color, design gradient, etc.
• -Logo on the back with website listed (https://www.kajufreightco.example)

```html
<!DOCTYPE html>
<html lang="en">
<head>
<meta charset="utf-8">
<title>KAJU Freightways Business Card</title>
<link href="https://fonts.googleapis.com/css2?family=Roboto+Slab:wght@400;700;900&display=swap" rel="stylesheet">
<style>
  :root {
    --stage: #8a8a8a;
    --card-dark: #232323;
    --card-light: #ffffff;
    --brand-green: #7cc242;
    --brand-navy: #173e4a;
    --ink-grey: #555b5e;
    --rule-grey: #b8bcbe;
    --silver: #b9b9b9;
  }
  * { margin: 0; padding: 0; box-sizing: border-box; }
  html, body { width: 1200px; height: 960px; overflow: hidden; }
  body {
    background: var(--stage);
    font-family: "Roboto Slab", Georgia, serif;
    position: relative;
  }
  .card {
    position: absolute;
    left: 250px;
    width: 700px;
    height: 400px;
    border-radius: 26px;
    border-bottom: 4px solid var(--brand-green);
    box-shadow: 0 10px 24px rgba(0,0,0,0.35);
    overflow: hidden;
  }
  .card-back { top: 50px; background: var(--card-dark); }
  .card-front { top: 500px; background: var(--card-light); }

  .mark {
    position: absolute;
    border-radius: 50%;
    display: flex;
    align-items: center;
    justify-content: center;
    font-weight: 900;
    letter-spacing: 1px;
  }
  .card-back .mark {
    left: 245px; top: 55px;
    width: 210px; height: 210px;
    border: 4px solid var(--silver);
    color: var(--silver);
    font-size: 58px;
  }
  .back-tagline {
    position: absolute; left: 0; right: 0; top: 292px;
    text-align: center;
    font-size: 22px; font-weight: 700; letter-spacing: 2px;
    color: var(--brand-green);
  }
  .back-website {
    position: absolute; left: 0; right: 0; top: 332px;
    text-align: center;
    font-size: 16px; font-weight: 400; letter-spacing: 0.5px;
    color: var(--silver);
  }
  .card-front .mark {
    left: 130px; top: 110px;
    width: 170px; height: 170px;
    border: 5px solid var(--brand-green);
    color: var(--brand-navy);
    font-size: 44px;
  }
  .divider {
    position: absolute;
    left: 340px; top: 95px;
    width: 1px; height: 190px;
    background: var(--rule-grey);
  }
  .identity { position: absolute; left: 370px; top: 100px; }
  .person-name {
    font-size: 26px; font-weight: 700;
    color: var(--brand-navy);
  }
  .person-title {
    font-size: 18px; font-weight: 700;
    color: var(--brand-green); margin-top: 2px;
  }
  .contact-list { list-style: none; margin-top: 16px; }
  .contact-list li {
    display: flex; align-items: center; gap: 10px;
    font-size: 16px; color: var(--ink-grey);
    line-height: 26px;
  }
  .contact-list svg { width: 14px; height: 14px; fill: var(--brand-navy); flex: none; }
  .address {
    position: absolute; left: 150px; top: 340px;
    display: flex; align-items: center; gap: 10px;
    font-size: 17px; color: var(--ink-grey);
  }
  .address svg { width: 16px; height: 20px; fill: var(--brand-navy); }
</style>
</head>
<body>
  <section class="card card-back" aria-label="Card back">
    <div class="mark">KAJU</div>
    <div class="back-tagline">#ALLKAJU</div>
    <div class="back-website">https://www.kajufreightco.example</div>
  </section>

  <section class="card card-front" aria-label="Card front">
    <div class="mark">KAJU</div>
    <div class="divider"></div>
    <div class="identity">
      <div class="person-name">DANA WHITFIELD</div>
      <div class="person-title">President</div>
      <ul class="contact-list">
        <li>
          <svg viewBox="0 0 24 24"><path d="M6.6 10.8a15.2 15.2 0 0 0 6.6 6.6l2.2-2.2a1 1 0 0 1 1-.25 11.4 11.4 0 0 0 3.6.57 1 1 0 0 1 1 1V20a1 1 0 0 1-1 1A17 17 0 0 1 3 4a1 1 0 0 1 1-1h3.5a1 1 0 0 1 1 1c0 1.25.2 2.45.57 3.57a1 1 0 0 1-.25 1z"/></svg>
          480-555-0172
        </li>
        <li>
          <svg viewBox="0 0 24 24"><path d="M2 5h20v14H2z M2 5l10 8 10-8" fill="none" stroke="#173e4a" stroke-width="2.5"/></svg>
          dana@kajufreight.example
        </li>
        <li>
          <svg viewBox="0 0 24 24"><circle cx="12" cy="12" r="10"/></svg>
          www.kajufreight.example
        </li>
      </ul>
    </div>
    <div class="address">
      <svg viewBox="0 0 16 20"><path d="M8 0a7 7 0 0 0-7 7c0 5 7 13 7 13s7-8 7-13a7 7 0 0 0-7-7zm0 10a3 3 0 1 1 0-6 3 3 0 0 1 0 6z"/></svg>
      2150 Saguaro Way, Phoenix, Arizona 85034
    </div>
  </section>
</body>
</html>
```